Dog grooming business card
This is a business card for m dog grooming business like it say above.
In the priorities box below I will have the text that I want on the card.

Industry/Entity Type

Business

Colors

Designer to choose colors to be used in the design.

Requirements
Must have
• My logo and the insurance stamp must be on the card.

Text it must have :

Professional grooming services
Email: lunabrisk@mailvale.net
Text or call 1 705 318 6052
TWF certified/member
Pet first aid certified
Next appointment ___________________________________
Nice to have
• Greens to match my logo

```html
<!DOCTYPE html>
<html lang="en">
<head>
<meta charset="utf-8">
<title>Luna Brisk – Grooming Business Card</title>
<link href="https://fonts.googleapis.com/css2?family=Libre+Baskerville:wght@400;700&display=swap" rel="stylesheet">
<style>
  :root {
    --backdrop: #d9d9d9;
    --paper: #fbfbfb;
    --charcoal: #2e2b2b;
    --ink: #1d1d1d;
    --leaf: #8cc63f;
    --leaf-deep: #5d8f22;
    --fold: #d4d4d4;
    --badge-blue: #2a78c8;
  }
  * { box-sizing: border-box; margin: 0; padding: 0; }
  html, body { width: 1200px; height: 864px; overflow: hidden; }
  body {
    background: var(--backdrop);
    font-family: "Libre Baskerville", Georgia, serif;
    color: var(--ink);
    position: relative;
  }
  .card {
    position: absolute;
    width: 540px;
    height: 310px;
    border-radius: 4px;
    box-shadow: 0 6px 18px rgba(0,0,0,.18);
    overflow: hidden;
  }
  .card-front { left: 40px; top: 277px; background: var(--paper); }
  .card-back { left: 620px; top: 277px; background: var(--charcoal); }

  .brand-panel {
    position: absolute; left: 0; top: 0; width: 236px; height: 100%;
    display: flex; align-items: center; justify-content: center; gap: 10px;
  }
  .brand-dot {
    width: 16px; height: 16px; border-radius: 50%; background: var(--leaf-deep);
  }
  .brand-name {
    font-weight: 700; font-size: 26px; color: var(--leaf-deep); letter-spacing: .5px;
  }
  .fold-line {
    position: absolute; left: 236px; top: 0; width: 1px; height: 100%;
    background: var(--fold);
  }
  .details {
    position: absolute; left: 237px; top: 0; right: 0; height: 100%;
    padding: 52px 18px 0;
    text-align: center;
    font-weight: 700; font-size: 15.5px; line-height: 1.35;
  }
  .insurance-badge {
    position: absolute; right: 14px; top: 14px; width: 64px; height: 34px;
    border: 2px solid var(--badge-blue); border-radius: 6px; background: #fff;
  }
  .appointment {
    position: absolute; left: 22px; right: 22px; bottom: 48px;
    display: flex; align-items: flex-end; gap: 14px;
    font-weight: 400; font-size: 14px;
  }
  .appointment-line { flex: 1; border-bottom: 1px solid var(--ink); height: 1px; margin-bottom: -18px; }

  .back-brand {
    position: absolute; inset: 0;
    display: flex; align-items: center; justify-content: center; gap: 12px;
    padding-bottom: 20px;
  }
  .back-brand .brand-dot { width: 20px; height: 20px; background: var(--leaf); }
  .back-brand .brand-name { font-size: 34px; color: var(--leaf); }
  .glow-line {
    position: absolute; left: 150px; right: 150px; top: 200px; height: 3px;
    border-radius: 2px;
    background: linear-gradient(90deg, transparent, var(--leaf), transparent);
    box-shadow: 0 0 14px 3px rgba(140,198,63,.45);
  }
</style>
</head>
<body>
  <section class="card card-front">
    <div class="brand-panel">
      <span class="brand-dot"></span>
      <span class="brand-name">Luna Brisk</span>
    </div>
    <div class="fold-line"></div>
    <div class="details">
      <div class="insurance-badge" role="img" aria-label="Insurance stamp"></div>
      <p>Professional grooming services</p>
      <p>1 705 318 6052</p>
      <p>lunabrisk@mailvale.net</p>
      <p>TWF certified/member</p>
      <p>Pet first aid certified</p>
      <div class="appointment">
        <span>Next appointment</span>
        <span class="appointment-line"></span>
      </div>
    </div>
  </section>

  <section class="card card-back">
    <div class="back-brand">
      <span class="brand-dot"></span>
      <span class="brand-name">Luna Brisk</span>
    </div>
    <div class="glow-line"></div>
  </section>
</body>
</html>
```